Landscape Construction and Design Company

We are a landscape construction and design company from New Jersey. We design and install landscapes and hardscapes for residential properties. The name of the company is Belwick's Landscape and Design LLC. We specialize mostly in planting trees and stone work, some water features. We would like to see design themes that include a tree or trees and a stone walkway or wall. We like earth tone colors. We like traditional to modern designs.

Target Market(s)

Homeowners

Industry/Entity Type

Landscape

Contact Information for Business Card

Nature themed design, earth tone colors, space for company name, address, phone numbers, email and website address

Logo Text

No text

Font styles to use
Serif

Colors

Designer to choose colors to be used in the design.

Requirements
Must have
• A tree or trees, similar to the ones uploaded in my supporting images
Nice to have
• I like trees similar to those in my uploaded supporting images. I like artistic, nature theme, earth tone colors
Should not have
• Pictures of real landscapes, cartoon looking logo or objects

```html
<!DOCTYPE html>
<html lang="en">
<head>
<meta charset="utf-8">
<title>Belwick's Landscape and Design LLC — Business Card</title>
<link rel="stylesheet" href="https://fonts.googleapis.com/css2?family=Cinzel:wght@500&family=Lato:wght@400&display=swap">
<style>
  :root {
    --canvas-bg: #ecebe8;
    --card-white: #ffffff;
    --leaf-green: #67a22c;
    --leaf-light: #b3d86a;
    --leaf-mid: #82b843;
    --leaf-dark: #4d8a30;
    --bark: #7a2a2a;
    --back-grey: #e2e2e2;
    --text-white: #ffffff;
  }
  * { margin: 0; padding: 0; box-sizing: border-box; }
  html, body {
    width: 1200px; height: 900px; overflow: hidden;
    background: var(--canvas-bg);
  }
  .canvas { position: relative; width: 1200px; height: 900px; }

  .card { position: absolute; box-shadow: 0 6px 18px rgba(0,0,0,0.18); overflow: hidden; }

  /* Front */
  .card-front {
    left: 178px; top: 74px; width: 588px; height: 364px;
    background: var(--card-white);
  }
  .front-panel { position: absolute; inset: 0; width: 588px; height: 364px; }
  .tree-illustration {
    position: absolute; left: 0; top: 0; width: 330px; height: 364px;
    background: linear-gradient(160deg, var(--leaf-light) 0%, var(--leaf-mid) 55%, var(--leaf-dark) 100%);
  }
  .front-info {
    position: absolute; right: 34px; top: 68px;
    text-align: right; color: var(--text-white);
    font-family: "Lato", sans-serif;
  }
  .holder-name {
    font-family: "Cinzel", serif; font-weight: 500;
    font-size: 24px; letter-spacing: 0.5px; line-height: 1.1;
  }
  .holder-title { font-size: 17px; line-height: 1.3; }
  .contact-list { list-style: none; margin-top: 93px; font-size: 17px; line-height: 22px; }
  .contact-list li { display: flex; justify-content: flex-end; align-items: center; gap: 4px; }
  .contact-list svg { width: 13px; height: 13px; flex: none; }
  .address { margin-top: 9px; font-size: 17px; line-height: 21px; }

  /* Back */
  .card-back {
    left: 388px; top: 505px; width: 566px; height: 352px;
    background: var(--back-grey);
  }
  .brand {
    position: absolute; left: 0; right: 0; top: 150px;
    display: flex; justify-content: center; align-items: center; gap: 14px;
  }
  .brand-dot { width: 22px; height: 22px; border-radius: 50%; background: var(--leaf-green); flex: none; }
  .brand-name {
    font-family: "Cinzel", serif; font-weight: 500;
    color: var(--leaf-green); font-size: 25px; line-height: 1.15; letter-spacing: 0.5px;
  }
  .services {
    position: absolute; left: 0; right: 0; top: 293px;
    text-align: center; font-family: "Lato", sans-serif;
    font-size: 17px; color: var(--leaf-green); letter-spacing: 0.2px;
  }
  .services .sep { color: var(--bark); padding: 0 2px; }
</style>
</head>
<body>
<main class="canvas">

  <section class="card card-front">
    <svg class="front-panel" viewBox="0 0 588 364" aria-hidden="true">
      <polygon points="168,0 588,0 588,364 190,364" fill="var(--leaf-green)"/>
    </svg>
    <div class="tree-illustration" role="img" aria-label="Illustrated tree with light and dark green leaves and a maroon trunk"></div>
    <div class="front-info">
      <h1 class="holder-name">MARCUS HALE</h1>
      <p class="holder-title">Managing Director</p>
      <ul class="contact-list">
        <li>444 555 7712
          <svg viewBox="0 0 16 16"><path d="M3 5c0-2 2-2 5-2s5 0 5 2v1h-3V5H6v1H3z M4 7h8l1 6H3z" fill="#fff"/></svg>
        </li>
        <li>info@youremail.com
          <svg viewBox="0 0 16 16"><rect x="1" y="3" width="14" height="10" fill="#fff"/><path d="M1 3l7 6 7-6" fill="none" stroke="var(--leaf-green)" stroke-width="1.3"/></svg>
        </li>
        <li>www.websitename.com
          <svg viewBox="0 0 16 16"><circle cx="8" cy="8" r="7" fill="#fff"/><path d="M1 8h14M8 1c-3 4-3 10 0 14M8 1c3 4 3 10 0 14" fill="none" stroke="var(--leaf-green)" stroke-width="1"/></svg>
        </li>
      </ul>
      <p class="address">421, Address line here<br>Country Name,45452</p>
    </div>
  </section>

  <section class="card card-back">
    <div class="brand">
      <span class="brand-dot" aria-hidden="true"></span>
      <p class="brand-name">Belwick's<br>Landscape and Design LLC</p>
    </div>
    <p class="services">PLANTING TREES <span class="sep">|</span> STONE WORK <span class="sep">|</span> WATER FEATURES</p>
  </section>

</main>
</body>
</html>
```